Web landing page design

- Create a Web Design (Uncoded - PSD layout only)

We need a single web page design to promote our service. This page will
acts as a landing page for users and also be utilized in social media
advertising. Please provide us with a cutting edge design. I have attached
a link for what the company is about. In essence we are a photo checking
service which reviews photos for retailers, hotels abd car dealerships to
check everything is good after a service has been performed. Whether it be
a new promotion, cleaning or just checking prices. I am looking for a
design to say that we do many photos and at a very cost effective price
(team based in Mexico)

Link: https://slidevault.example/view/qTr8nWx2LpZk4mHcYdJs/
*Deadline*
5 days
*Updates*

- The Start Here box needs to look like this:

-Start Here (heading)
-A box for email addresses to be entered
-Then a check box with "Yes, I have read and agree to the Privacy Policy
and agree to receive email marketing from Plumora88'
-A submit button

All of this information needs to be in one box please. And please feel
free to contact me if you have any questions about this.

*Target Market(s)*
Retail business, Merchandising companies, Rental property owners, Car
dealers
Updates

Please can you submit entries. I am just looking for a tidy to a presentation already created. Just needs design touches.

Target Market(s)

Ability for audience to understand concept quickly
Benefits to why to use the product stand out
Technology driven approach

Industry/Entity Type

Retail

Number of Pages Required

1 page

Colors
0792cd

Requirements
Must have
• Clean and modern design

```html
<!DOCTYPE html>
<html lang="en">
<head>
<meta charset="UTF-8">
<title>Plumora88 — Transform Retail Execution</title>
<link rel="stylesheet" href="https://fonts.googleapis.com/css2?family=Montserrat:wght@400;500;600;700&display=swap">
<style>
  :root {
    --brand: #0792cd;
    --brand-glass: rgba(7, 146, 205, 0.82);
    --white: #ffffff;
    --ink-muted: #6f6f6f;
    --line: #d5d5d5;
    --photo-dark: #2a2f36;
    --photo-mid: #5b5a5c;
    --photo-skin: #b08a78;
  }
  * { box-sizing: border-box; margin: 0; padding: 0; }
  html, body { width: 1200px; height: 778px; overflow: hidden; }
  body { font-family: "Montserrat", sans-serif; color: var(--white); background: var(--brand); }

  .page { position: relative; width: 1200px; height: 778px; }

  .hero { position: absolute; left: 0; top: 0; width: 1200px; height: 575px; overflow: hidden; }
  .hero-photo {
    position: absolute; inset: 0;
    background:
      radial-gradient(ellipse 380px 240px at 560px 300px, rgba(190,150,130,0.75), transparent 70%),
      radial-gradient(ellipse 260px 200px at 860px 200px, rgba(170,130,115,0.6), transparent 70%),
      radial-gradient(ellipse 300px 260px at 1100px 120px, rgba(120,60,50,0.55), transparent 70%),
      linear-gradient(120deg, var(--photo-dark) 0%, var(--photo-mid) 45%, var(--photo-skin) 70%, var(--photo-dark) 100%);
  }
  .hero-shade { position: absolute; inset: 0; background: rgba(20, 25, 32, 0.28); }

  .brand { position: absolute; left: 86px; top: 68px; }
  .brand-name { font-weight: 700; font-size: 26px; line-height: 1; color: var(--white); letter-spacing: 0.3px; }

  .nav { position: absolute; right: 87px; top: 42px; display: flex; align-items: center; gap: 0; }
  .nav-link { font-size: 15px; font-weight: 500; color: var(--white); text-decoration: none; margin-right: 34px; }
  .nav-link:last-child { margin-right: 0; }
  .nav-cta { background: var(--brand); padding: 0 17px; height: 39px; line-height: 39px; border-radius: 2px; font-weight: 500; }

  .headline {
    position: absolute; left: 86px; top: 283px; width: 529px; height: 106px;
    background: var(--brand-glass);
    display: flex; align-items: center; justify-content: center; text-align: center;
    font-size: 28px; font-weight: 700; line-height: 1.25; text-transform: uppercase; white-space: nowrap;
  }

  .signup {
    position: absolute; left: 840px; top: 224px; width: 273px; height: 224px;
    background: var(--white); padding: 26px 9px 0;
  }
  .signup-title { text-align: center; color: var(--brand); font-size: 23px; font-weight: 700; line-height: 1.2; }
  .signup-email {
    display: block; width: 247px; height: 35px; margin: 11px 0 0 1px;
    border: 2px solid var(--line); padding: 0 8px;
    font-family: inherit; font-size: 13px; color: var(--ink-muted); background: var(--white);
  }
  .signup-email::placeholder { color: #b0b0b0; }
  .signup-consent { display: flex; gap: 8px; margin-top: 13px; padding-left: 3px; color: var(--ink-muted); font-size: 10px; line-height: 1.55; font-weight: 500; }
  .signup-check { flex: none; width: 14px; height: 14px; margin-top: 3px; border: 1.5px solid #8a8a8a; border-radius: 2px; }
  .signup-submit {
    display: block; width: 186px; height: 35px; margin: 12px 0 0 34px;
    background: var(--brand); border: none; color: var(--white);
    font-family: inherit; font-size: 17px; font-weight: 600; letter-spacing: 0.5px;
  }

  .stats { position: absolute; left: 0; top: 575px; width: 1200px; height: 203px; background: var(--brand); }
  .stat { position: absolute; top: 33px; width: 240px; margin-left: -120px; text-align: center; }
  .stat-ring {
    width: 110px; height: 110px; margin: 0 auto; border: 3px solid var(--white); border-radius: 50%;
    display: flex; align-items: center; justify-content: center;
    font-size: 36px; font-weight: 700; letter-spacing: -0.5px; white-space: nowrap;
  }
  .stat-ring-wide { font-size: 32px; letter-spacing: -1px; }
  .stat-label { margin-top: 10px; font-size: 17.5px; font-weight: 400; white-space: nowrap; }
</style>
</head>
<body>
<div class="page">
  <section class="hero">
    <div class="hero-photo" role="img" aria-label="Close-up of hands holding a white smartphone, blurred background"></div>
    <div class="hero-shade"></div>

    <div class="brand">
      <span class="brand-name">Plumora88</span>
    </div>

    <nav class="nav">
      <a class="nav-link" href="#">About</a>
      <a class="nav-link" href="#">Results</a>
      <a class="nav-link" href="#">How</a>
      <a class="nav-link nav-cta" href="#">Free Trial</a>
    </nav>

    <h1 class="headline">Transform retail execution<br>with a simple photo</h1>

    <form class="signup">
      <h2 class="signup-title">START HERE</h2>
      <input class="signup-email" type="email" placeholder="Email*">
      <div class="signup-consent">
        <span class="signup-check"></span>
        <span>Yes, I have read and agree to the Privacy Policy and agree to receive email marketing from Plumora88</span>
      </div>
      <button class="signup-submit" type="button">SUBMIT</button>
    </form>
  </section>

  <section class="stats">
    <div class="stat" style="left:245px"><div class="stat-ring">2.2m</div><p class="stat-label">Photos reviewed last year</p></div>
    <div class="stat" style="left:513px"><div class="stat-ring">5p</div><p class="stat-label">From per photo reviewed</p></div>
    <div class="stat" style="left:755px"><div class="stat-ring stat-ring-wide">97.2%</div><p class="stat-label">Average compliance</p></div>
    <div class="stat" style="left:973px"><div class="stat-ring stat-ring-wide">3-8%</div><p class="stat-label">Sales increase</p></div>
  </section>
</div>
</body>
</html>
```